WordPress Design for both website and landing page for an expert

I need a clean and stylish design for my new website. I work as an expert (see attached file WHY HOW WHAT), my product is expert opinion (reports) for company evaluations You can use all of the attached pictures colored or black / white. The person is me, you can add other pictures, if you want. The design should be clean and stylish, so you could use white, black, gray, silver and / or one additional color. I have added an idea about my website, see attached file CONCEPT WEBSITE If you have any more information, please do not hesitate to contact us 'Hesitate to ask me ...

```html
<!DOCTYPE html>
<html lang="en">
<head>
<meta charset="utf-8">
<title>Elias Wendt – Company Valuations</title>
<link rel="stylesheet" href="https://fonts.googleapis.com/css2?family=Source+Sans+3:wght@300;400;600;700&display=swap">
<style>
:root{
  --ink:#222630;
  --muted:#6d7280;
  --brand:#1f4e9c;
  --brand-dark:#1b3f7e;
  --button:#2356a3;
  --soft:#f4f5f8;
  --line:#e3e5ea;
  --icon-bg:#dde5f0;
  --footer-shape:#a9a9ab;
  --logo:#7b7f88;
}
*{box-sizing:border-box;margin:0;padding:0}
html,body{width:1097px;height:1200px;overflow:hidden;background:#fff}
body{position:relative;font-family:"Source Sans 3",Arial,sans-serif;color:var(--ink)}
.page{position:absolute;top:24px;width:512px;height:1152px;background:#fff;overflow:hidden;box-shadow:0 0 6px rgba(0,0,0,.18)}
.page--portrait{left:26px}
.page--skyline{left:558px}
.abs{position:absolute}

/* header */
.site-header{position:absolute;left:0;top:0;width:512px;height:42px;background:#fff;z-index:3}
.brand{position:absolute;left:48px;top:10px;display:flex;align-items:center;gap:5px;font-size:10px;letter-spacing:1.6px;color:var(--logo);font-weight:400}
.brand-dot{width:9px;height:9px;border-radius:50%;background:var(--logo)}
.main-nav{position:absolute;left:194px;top:16px;display:flex;gap:19px;font-size:6.4px;letter-spacing:.3px;color:#3a3e48}

/* hero */
.hero{position:absolute;left:0;top:42px;width:512px;height:228px;overflow:hidden}
.hero--portrait{background:var(--soft)}
.hero-ring{position:absolute;left:250px;top:-40px;width:380px;height:320px;border-radius:50%;background:#fafafb}
.hero-photo{position:absolute;left:-95px;top:-48px;width:345px;height:318px;border-radius:50%;background:radial-gradient(circle at 60% 40%,#d9d6d2,#a9a39c 60%,#7b7670)}
.hero-title{font-weight:700;color:var(--brand);font-size:22px;letter-spacing:.3px}
.hero-sub{font-weight:400;font-size:16px;line-height:18px}
.hero-text{font-weight:300;font-size:9.6px;line-height:13px;color:var(--muted)}
.btn{position:absolute;display:flex;align-items:center;justify-content:center;background:var(--button);color:#fff;font-size:6.6px;font-weight:600;letter-spacing:.4px;border-radius:10px}
.btn--hero{background:var(--brand-dark);width:66px;height:18px}
.slider-arrows{position:absolute;display:flex;gap:4px}
.slider-arrows span{width:17px;height:15px;border:1px solid #cfd2d8;display:flex;align-items:center;justify-content:center;background:#fff}
.hero--skyline{background:linear-gradient(180deg,#1a74dc 0%,#1c5fb9 45%,#243a6b 70%,#3a3340 85%,#24324f 100%)}
.hero--skyline .hero-title,.hero--skyline .hero-sub{color:#fff}
.hero--skyline .hero-text{color:#d6e4f7}
.slider-arrows--dark span{border:none;background:rgba(15,30,60,.6)}

/* features */
.features{position:absolute;left:0;top:270px;width:512px;height:232px;background:linear-gradient(180deg,#fbfbfc,#eef0f4)}
.section-title{position:absolute;left:0;width:512px;text-align:center;font-size:14.5px;font-weight:400}
.feature{position:absolute;width:110px;text-align:center;top:77px}
.feature-icon{width:52px;height:52px;border-radius:50%;background:var(--icon-bg);margin:0 auto;display:flex;align-items:center;justify-content:center}
.feature-name{font-size:10px;margin-top:10px}
.feature-text{font-size:6px;line-height:11px;color:var(--muted);margin-top:6px;font-weight:300}

/* quality band */
.promise{position:absolute;left:0;top:502px;width:512px;height:156px;background:linear-gradient(120deg,#c79a7a 0%,#efe6dc 35%,#f7f3ee 60%,#d9d6d4 100%)}
.promise-text{position:absolute;left:0;width:512px;text-align:center;font-size:6px;color:#2c2f36}

/* faq */
.faq-card{position:absolute;left:74px;top:732px;width:364px;height:146px;border-radius:12px;background:#fff;box-shadow:0 0 6px rgba(0,0,0,.09)}
.faq-row{position:absolute;left:16px;width:332px;height:18px;border-bottom:1px solid var(--line);font-size:5.8px;display:flex;justify-content:space-between;align-items:center}
.faq-lead{position:absolute;left:17px;top:98px;font-size:5.8px;color:var(--brand);font-style:italic;font-weight:600}
.faq-note{position:absolute;left:17px;top:113px;width:320px;font-size:5px;line-height:8.5px;color:#9a9ea8}

/* newsletter + footer */
.divider{position:absolute;left:44px;top:926px;width:430px;height:1px;background:var(--line)}
.lower-backdrop{position:absolute;left:0;top:880px;width:512px;height:272px;background:linear-gradient(180deg,#fff 0%,#f2f4f8 45%,#e4e7ec 100%)}
.page--skyline .lower-backdrop{background:#fff}
.cta-text{position:absolute;left:44px;top:952px;font-size:9.2px;line-height:14px;font-weight:600;color:#2a2d35}
.email-field{position:absolute;left:279px;top:956px;width:175px;height:21px;border-radius:11px;background:#fff;box-shadow:0 0 5px rgba(0,0,0,.1);font-size:6px;color:#8a8e98;display:flex;align-items:center;justify-content:space-between;padding:0 12px}
.footer-shape{position:absolute;left:0;top:1000px}
.footer-brand{position:absolute;left:48px;top:1050px;display:flex;align-items:center;gap:5px;font-size:8.5px;letter-spacing:1.4px;color:var(--logo)}
.footer-links{position:absolute;font-size:6.3px;color:#fff;line-height:11.7px}
.footer-links--pages{left:177px;top:1052px}
.footer-links--info{left:273px;top:1052px;line-height:13.3px}
.social{position:absolute;left:390px;top:1044px;display:flex;gap:5.5px}
.social span{width:16px;height:16px;border-radius:50%;border:1px solid var(--brand)}
.copyright{position:absolute;left:0;width:512px;top:1137px;text-align:center;font-size:5.2px;color:#fff}
</style>
</head>
<body>

<!-- Variant 1: portrait hero -->
<div class="page page--portrait">
  <header class="site-header">
    <div class="brand"><span class="brand-dot"></span>ELIAS WENDT</div>
    <nav class="main-nav"><span>HOME</span><span>WHAT I DO</span><span>WHY I DO IT &amp; HOW I DO IT</span><span>ABOUT ME</span><span>CONTACT</span></nav>
  </header>

  <section class="hero hero--portrait">
    <div class="hero-ring"></div>
    <div class="hero-photo" role="img" aria-label="Portrait of the expert in a white shirt leaning on a railing"></div>
    <h1 class="abs hero-title" style="left:302px;top:28px">ELIAS WENDT</h1>
    <p class="abs hero-sub" style="left:303px;top:58px">Expert for company<br>valuations</p>
    <p class="abs hero-text" style="left:303px;top:98px">You need an opinion to determine the value<br>of your company</p>
    <div class="btn btn--hero" style="left:303px;top:138px">CONTACT US</div>
    <div class="slider-arrows" style="left:303px;top:182px">
      <span><svg width="5" height="7"><path d="M4 1L1 3.5 4 6" stroke="#777" fill="none"/></svg></span>
      <span><svg width="5" height="7"><path d="M1 1l3 2.5L1 6" stroke="#777" fill="none"/></svg></span>
    </div>
  </section>

  <section class="features" role="img" aria-label="Faint background of financial charts">
    <h2 class="section-title" style="top:42px">Why Choose Us</h2>
    <div class="feature" style="left:60px">
      <div class="feature-icon"><svg width="20" height="20" viewBox="0 0 20 20" fill="none" stroke="#2356a3" stroke-width="1.4"><circle cx="11" cy="11" r="6"/><path d="M11 8v3l2 1M9 3h4M1 9h4M2 12h3M3 15h3"/></svg></div>
      <div class="feature-name">Fast</div>
      <div class="feature-text">You will receive your report promptly (within a maximum of 21 days after receipt of all required documents)</div>
    </div>
    <div class="feature" style="left:201px">
      <div class="feature-icon"><svg width="20" height="20" viewBox="0 0 20 20" fill="none" stroke="#2356a3" stroke-width="1.4"><circle cx="10" cy="8" r="6"/><path d="M10 5l1 2h2l-1.5 1.3.6 2L10 9l-2.1 1.3.6-2L7 7h2zM6 13l-2 5 3-1 1 2 2-4M14 13l2 5-3-1-1 2-2-4"/></svg></div>
      <div class="feature-name">Certified</div>
      <div class="feature-text">You receive a qualified and reliable report from a certified expert (highest acceptance by all parties)</div>
    </div>
    <div class="feature" style="left:342px">
      <div class="feature-icon"><svg width="20" height="20" viewBox="0 0 20 20" fill="none" stroke="#2356a3" stroke-width="1.4"><path d="M3 9h3v9H3zM6 9l4-7c2 0 2 2 1.5 4H17c1 0 1.6 1 1.4 2l-1.4 7c-.2.8-.8 1-1.5 1H6"/></svg></div>
      <div class="feature-name">Understandable</div>
      <div class="feature-text">Your report will be logical and comprehensible for you and will not contain any "technical Chinese"</div>
    </div>
  </section>

  <section class="promise" role="img" aria-label="Hands writing with a pen beside a laptop and printed charts">
    <h2 class="section-title" style="top:42px">My Quality Promise</h2>
    <p class="promise-text" style="top:65px">should the advised date for the preparation of the report be exceeded, you will receive the report free of chare</p>
    <div class="btn" style="left:211px;top:81px;width:90px;height:18px">I WAIVE MY FEE</div>
  </section>

  <div class="lower-backdrop" role="img" aria-label="Faint city skyline fading into the footer"></div>
  <h2 class="section-title" style="top:700px">FAQ'S</h2>
  <div class="faq-card">
    <div class="faq-row" style="top:12px"><span>What are the buying motives of the customers?</span><svg width="6" height="4"><path d="M1 1l2 2 2-2" stroke="#333" fill="none"/></svg></div>
    <div class="faq-row" style="top:30px"><span>You want to sell shares of your company or your entire company?</span><svg width="6" height="4"><path d="M1 1l2 2 2-2" stroke="#333" fill="none"/></svg></div>
    <div class="faq-row" style="top:47px"><span>You want to transfer your business to your heirs and need a valuation for the tax office?</span><svg width="6" height="4"><path d="M1 1l2 2 2-2" stroke="#333" fill="none"/></svg></div>
    <div class="faq-row" style="top:65px"><span>What are the buying motives of the customers?</span><svg width="6" height="4"><path d="M1 1l2 2 2-2" stroke="#333" fill="none"/></svg></div>
    <p class="faq-lead">Have your company evaluated by a qualified expert and avoid many (unnecessary) quarrels.</p>
    <p class="faq-note">Note: The cost of a report are always disproportionately cheaper than the cost of legal disputes. And that detached from the psychological burden of such an argument ...</p>
  </div>

  <div class="divider"></div>
  <p class="cta-text">Let's talk about how can help you<br>better understand your users.</p>
  <div class="email-field"><span>Enter Your Email Address</span><svg width="11" height="6"><path d="M0 3h9M7 1l2 2-2 2" stroke="#2356a3" stroke-width="1.3" fill="none"/></svg></div>

  <svg class="footer-shape" width="512" height="152" viewBox="0 1000 512 152"><path d="M112 1152C112 1070 150 1022 212 1022C250 1022 285 1042 512 1128L512 1152Z" fill="#a9a9ab"/></svg>
  <div class="footer-brand"><span class="brand-dot"></span>ELIAS WENDT</div>
  <div class="footer-links footer-links--pages">Home<br>What I Do<br>Why I Do It &amp; How I Do It<br>About Me<br>Contact</div>
  <div class="footer-links footer-links--info">Faq<br>Privacy policy<br>Sitemap</div>
  <div class="social"><span></span><span></span><span></span><span></span></div>
  <p class="copyright">© 2018 Copyrights.Elias Wendt.All Rights Reserved</p>
</div>

<!-- Variant 2: skyline hero -->
<div class="page page--skyline">
  <header class="site-header">
    <div class="brand"><span class="brand-dot"></span>ELIAS WENDT</div>
    <nav class="main-nav"><span>HOME</span><span>WHAT I DO</span><span>WHY I DO IT &amp; HOW I DO IT</span><span>ABOUT ME</span><span>CONTACT</span></nav>
  </header>

  <section class="hero hero--skyline" role="img" aria-label="Night skyline of a river city with a tall tower and bridge">
    <h1 class="abs hero-title" style="left:46px;top:36px">ELIAS WENDT</h1>
    <p class="abs hero-sub" style="left:48px;top:64px">Expert for company valuations</p>
    <p class="abs hero-text" style="left:48px;top:87px">You need an opinion to determine the value<br>of your company</p>
    <div class="btn btn--hero" style="left:48px;top:157px">CONTACT US</div>
    <div class="slider-arrows slider-arrows--dark" style="left:7px;top:199px">
      <span><svg width="5" height="7"><path d="M4 1L1 3.5 4 6" stroke="#fff" fill="none"/></svg></span>
      <span><svg width="5" height="7"><path d="M1 1l3 2.5L1 6" stroke="#fff" fill="none"/></svg></span>
    </div>
  </section>

  <section class="features" role="img" aria-label="Faint background of financial charts">
    <h2 class="section-title" style="top:42px">Why Choose Us</h2>
    <div class="feature" style="left:60px">
      <div class="feature-icon"><svg width="20" height="20" viewBox="0 0 20 20" fill="none" stroke="#2356a3" stroke-width="1.4"><circle cx="11" cy="11" r="6"/><path d="M11 8v3l2 1M9 3h4M1 9h4M2 12h3M3 15h3"/></svg></div>
      <div class="feature-name">Fast</div>
      <div class="feature-text">You will receive your report promptly (within a maximum of 21 days after receipt of all required documents)</div>
    </div>
    <div class="feature" style="left:201px">
      <div class="feature-icon"><svg width="20" height="20" viewBox="0 0 20 20" fill="none" stroke="#2356a3" stroke-width="1.4"><circle cx="10" cy="8" r="6"/><path d="M10 5l1 2h2l-1.5 1.3.6 2L10 9l-2.1 1.3.6-2L7 7h2zM6 13l-2 5 3-1 1 2 2-4M14 13l2 5-3-1-1 2-2-4"/></svg></div>
      <div class="feature-name">Certified</div>
      <div class="feature-text">You receive a qualified and reliable report from a certified expert (highest acceptance by all parties)</div>
    </div>
    <div class="feature" style="left:342px">
      <div class="feature-icon"><svg width="20" height="20" viewBox="0 0 20 20" fill="none" stroke="#2356a3" stroke-width="1.4"><path d="M3 9h3v9H3zM6 9l4-7c2 0 2 2 1.5 4H17c1 0 1.6 1 1.4 2l-1.4 7c-.2.8-.8 1-1.5 1H6"/></svg></div>
      <div class="feature-name">Understandable</div>
      <div class="feature-text">Your report will be logical and comprehensible for you and will not contain any "technical Chinese"</div>
    </div>
  </section>

  <section class="promise" role="img" aria-label="Hands writing with a pen beside a laptop and printed charts">
    <h2 class="section-title" style="top:42px">My Quality Promise</h2>
    <p class="promise-text" style="top:65px">should the advised date for the preparation of the report be exceeded, you will receive the report free of chare</p>
    <div class="btn" style="left:211px;top:81px;width:90px;height:18px">I WAIVE MY FEE</div>
  </section>

  <div class="lower-backdrop"></div>
  <h2 class="section-title" style="top:700px">FAQ'S</h2>
  <div class="faq-card">
    <div class="faq-row" style="top:12px"><span>What are the buying motives of the customers?</span><svg width="6" height="4"><path d="M1 1l2 2 2-2" stroke="#333" fill="none"/></svg></div>
    <div class="faq-row" style="top:30px"><span>You want to sell shares of your company or your entire company?</span><svg width="6" height="4"><path d="M1 1l2 2 2-2" stroke="#333" fill="none"/></svg></div>
    <div class="faq-row" style="top:47px"><span>You want to transfer your business to your heirs and need a valuation for the tax office?</span><svg width="6" height="4"><path d="M1 1l2 2 2-2" stroke="#333" fill="none"/></svg></div>
    <div class="faq-row" style="top:65px"><span>What are the buying motives of the customers?</span><svg width="6" height="4"><path d="M1 1l2 2 2-2" stroke="#333" fill="none"/></svg></div>
    <p class="faq-lead">Have your company evaluated by a qualified expert and avoid many (unnecessary) quarrels.</p>
    <p class="faq-note">Note: The cost of a report are always disproportionately cheaper than the cost of legal disputes. And that detached from the psychological burden of such an argument ...</p>
  </div>

  <div class="divider"></div>
  <p class="cta-text">Let's talk about how can help you<br>better understand your users.</p>
  <div class="email-field"><span>Enter Your Email Address</span><svg width="11" height="6"><path d="M0 3h9M7 1l2 2-2 2" stroke="#2356a3" stroke-width="1.3" fill="none"/></svg></div>

  <svg class="footer-shape" width="512" height="152" viewBox="0 1000 512 152"><path d="M112 1152C112 1070 150 1022 212 1022C250 1022 285 1042 512 1128L512 1152Z" fill="#a9a9ab"/></svg>
  <div class="footer-brand"><span class="brand-dot"></span>ELIAS WENDT</div>
  <div class="footer-links footer-links--pages">Home<br>What I Do<br>Why I Do It &amp; How I Do It<br>About Me<br>Contact</div>
  <div class="footer-links footer-links--info">Faq<br>Privacy policy<br>Sitemap</div>
  <div class="social"><span></span><span></span><span></span><span></span></div>
  <p class="copyright">© 2018 Copyrights.Elias Wendt.All Rights Reserved</p>
</div>

</body>
</html>
```